COFFEE RALLY // COFFEE PATHWAYS // STEADY COFFEE

website that looks kind of: www.trevandor.com OR PIXELHARBR
I sell coffee to sports teams at a very low price and they make the profit for whatever they are looking to raise money for. This is a tool for them to raise money.
I need help creating not just the website but a catchy name for this project.
Now students don't need to wash cars to raise funds, they have my coffee they can sell to turn it into their own profits.

Target Market(s)

sports teams, schools, churches, fundraisers.

Industry/Entity Type

coffee // fundraiser

Coding

Coded - Design and coding required

Number of Pages Required

1 page

Font styles to use
Serif

Colors
0054AA
0677BA
7BADD7
CADEEF
E8F1F8

Requirements
Must have
• Video of how it works (steps) // Get started button // personalize your coffee bag
Nice to have
• Lumvek.com for example as a name for the website

```html
<!DOCTYPE html>
<html lang="en">
<head>
<meta charset="utf-8">
<title>Lumvek – Fundraise With Custom Coffee</title>
<link href="https://fonts.googleapis.com/css2?family=Bebas+Neue&family=Poppins:wght@300;400;500;600&display=swap" rel="stylesheet">
<style>
:root{
  --blue-dark:#0054AA;
  --blue:#0677BA;
  --blue-mid:#7BADD7;
  --blue-light:#CADEEF;
  --blue-pale:#E8F1F8;
  --ink:#141414;
  --muted:#6b6b6b;
  --white:#ffffff;
}
*{margin:0;padding:0;box-sizing:border-box}
html,body{width:1200px;height:4781px;overflow:hidden}
body{position:relative;font-family:'Poppins',sans-serif;color:var(--ink);background:var(--white)}
.abs{position:absolute}
.btn{position:absolute;display:inline-flex;align-items:center;justify-content:center;height:40px;padding:0;border-radius:20px;background:linear-gradient(90deg,var(--blue),var(--blue-dark));color:var(--white);font-size:13px;font-weight:500;letter-spacing:.3px;text-transform:uppercase;box-shadow:0 4px 10px rgba(0,84,170,.25)}
.photo{position:absolute;overflow:hidden}

/* top bar */
.topbar{left:0;top:0;width:1200px;height:33px;background:var(--blue-dark);color:var(--white);font-size:12px}
.topbar span{position:absolute;top:8px;display:flex;align-items:center;gap:8px}

/* hero */
.hero{left:0;top:33px;width:1200px;height:700px;background:var(--blue-light)}
.nav{position:absolute;top:0;left:0;width:1200px;font-size:11.5px;color:var(--ink)}
.nav a{position:absolute;top:34px;text-decoration:none;color:inherit;white-space:nowrap}
.nav .active{color:var(--blue-dark);border-bottom:1px solid var(--blue-dark);padding-bottom:3px}
.brand{position:absolute;left:553px;top:17px;font-size:34px;line-height:40px;font-weight:400;color:var(--blue-dark)}
.login{position:absolute;left:1064px;top:20px;width:76px;height:36px;border:1.5px solid var(--blue-dark);border-radius:18px;color:var(--blue-dark);font-size:12px;display:flex;align-items:center;justify-content:center}
.hero-title{position:absolute;left:112px;top:212px;font-family:'Bebas Neue',sans-serif;font-weight:400;font-size:48px;line-height:55px;color:var(--white);letter-spacing:.5px}
.hero-title .accent{color:var(--blue-dark)}
.arrow{position:absolute;top:268px;width:40px;height:40px;border-radius:50%;background:rgba(255,255,255,.35);display:flex;align-items:center;justify-content:center}

/* headings */
.h2{position:absolute;font-size:31px;line-height:37px;font-weight:400;text-transform:uppercase}
.h2 .blue{color:var(--blue-dark)}
.h3{position:absolute;font-size:28px;line-height:37px;font-weight:400;text-transform:uppercase;color:var(--ink)}
.copy{position:absolute;font-size:11.5px;line-height:19.5px;color:var(--muted)}
.copy p{margin-bottom:10px}

/* flavors */
.flavors-sub{position:absolute;left:0;top:1396px;width:1200px;text-align:center;font-size:13px;color:var(--ink)}
.card{position:absolute;top:1447px;width:300px;height:412px;background:var(--white);border-radius:10px;overflow:hidden;text-align:center}
.card .beans{position:absolute;left:0;top:0;width:300px;height:166px;background:radial-gradient(circle at 30% 40%,#6b3f22,#2b170c 80%)}
.card .bag{position:absolute;left:88px;top:50px;width:124px;height:190px;border-radius:62px 62px 8px 8px;background:linear-gradient(160deg,#d7bb98,#b89470)}
.card h4{position:absolute;left:0;top:268px;width:300px;font-size:16px;font-weight:500;letter-spacing:.3px}
.card .size{position:absolute;left:0;top:292px;width:300px;font-size:10px;color:var(--muted)}
.card .price{position:absolute;left:0;top:312px;width:300px;font-size:18px;font-weight:600;color:var(--blue-dark)}
.card .btn{top:341px;left:88px;width:124px}

/* stats */
.stats{position:absolute;left:661px;top:2549px;font-size:11px;color:var(--muted);list-style:none}
.stats li{height:28px;display:flex;align-items:center;gap:14px}
.ring{position:absolute;width:58px;height:58px;border-radius:50%;border:7px solid var(--blue-light)}

/* reviews */
.reviews{left:0;top:3245px;width:1200px;height:471px;background:linear-gradient(135deg,#134f95,var(--blue-dark) 60%,#0a3f86);overflow:hidden}
.reviews .halo{position:absolute;left:325px;top:78px;width:430px;height:430px;border-radius:50%;border:40px solid rgba(255,255,255,.06)}
.reviews h2{position:absolute;left:0;top:72px;width:1200px;text-align:center;font-size:31px;font-weight:400;color:var(--white)}
.reviews h2 .dark{color:var(--ink)}
.reviews .sub{position:absolute;left:0;top:113px;width:1200px;text-align:center;font-size:12px;color:var(--white)}
.review{position:absolute;top:189px;width:316px;height:208px;background:rgba(10,60,130,.55);border-radius:10px;color:var(--white);font-size:11px;line-height:20px}
.review .q{position:absolute;left:30px;top:-22px;width:42px;height:42px;border-radius:50%;background:var(--white);display:flex;align-items:center;justify-content:center;color:var(--blue-dark);font-size:28px;font-weight:600;line-height:1}
.review p{position:absolute;left:28px;top:45px;width:270px}
.review .who{position:absolute;left:28px;top:140px;font-size:12px}
.review .stars{position:absolute;left:48px;top:160px;color:#f6c42b;font-size:11px;letter-spacing:2px}

/* footer */
.footer-h{position:absolute;top:4531px;font-size:13px;color:var(--blue-dark);text-transform:uppercase;letter-spacing:.3px}
.links{position:absolute;top:4559px;list-style:none;font-size:11px;color:var(--white)}
.links li{height:22.5px}
.links li::before{content:"•";margin-right:10px;color:var(--white)}
</style>
</head>
<body>

<div class="abs topbar">
  <span style="left:60px">
    <svg width="14" height="14" viewBox="0 0 24 24"><path fill="#fff" d="M6.6 10.8a15 15 0 0 0 6.6 6.6l2.2-2.2c.3-.3.7-.4 1-.2 1.1.4 2.3.6 3.6.6.6 0 1 .4 1 1V20c0 .6-.4 1-1 1A17 17 0 0 1 3 4c0-.6.4-1 1-1h3.5c.6 0 1 .4 1 1 0 1.3.2 2.5.6 3.6.1.3 0 .7-.2 1z"/></svg>
    555-014-2398
  </span>
  <span style="left:946px">
    <svg width="15" height="12" viewBox="0 0 24 18"><rect x="1" y="1" width="22" height="16" rx="2" fill="none" stroke="#fff" stroke-width="2"/><path d="M2 2l10 8 10-8" fill="none" stroke="#fff" stroke-width="2"/></svg>
    hello@lumvekmail.com
  </span>
</div>

<header class="abs hero">
  <nav class="nav">
    <a class="active" style="left:316px">Home</a>
    <a style="left:370px">Sell Online</a>
    <a style="left:453px">About Lumvek</a>
    <div class="brand">Lumvek</div>
    <a style="left:682px">Fundraise</a>
    <a style="left:755px">Customize</a>
    <a style="left:842px">Explore</a>
    <div class="login">LOGIN</div>
  </nav>

  <div class="arrow" style="left:40px">
    <svg width="10" height="14" viewBox="0 0 10 14"><path d="M8 1L2 7l6 6" fill="none" stroke="#fff" stroke-width="2"/></svg>
  </div>
  <div class="arrow" style="left:1120px">
    <svg width="10" height="14" viewBox="0 0 10 14"><path d="M2 1l6 6-6 6" fill="none" stroke="#fff" stroke-width="2"/></svg>
  </div>

  <h1 class="hero-title">HEART OF THE ANDES<br><span class="accent">GROWN AT A HIGH ALTITUDE</span><br>FOR HIGH QUALITY !</h1>
  <div class="btn" style="left:112px;top:388px;width:122px">SHOP NOW</div>

  <div class="photo" role="img" aria-label="Athlete sprinting forward behind the product" style="left:810px;top:110px;width:240px;height:560px;border-radius:120px 120px 60px 60px;background:linear-gradient(180deg,#9fb2c4,#5b6c80 55%,#2a323c)"></div>
  <div class="photo" role="img" aria-label="Labelled kraft coffee bag product with roasted beans at its base" style="left:642px;top:245px;width:250px;height:390px;border-radius:18px 18px 40px 40px;background:linear-gradient(160deg,#d9bf9d,#b38d67 70%,#5a3520)"></div>

  <svg class="abs" style="left:0;top:0" width="1200" height="700" viewBox="0 0 1200 700">
    <path d="M0 632 C200 585 420 610 620 625 C820 640 1000 700 1200 665 L1200 700 L0 700Z" fill="#fff"/>
  </svg>
</header>

<section>
  <div class="photo" role="img" aria-label="Coffee beans arranged in heart and cup shapes" style="left:297px;top:790px;width:270px;height:380px;border-radius:40%;background:radial-gradient(ellipse at 55% 30%,#6e4125,#3b2010 55%,rgba(255,255,255,0) 72%)"></div>
  <div class="photo" role="img" aria-label="Rugby team in a huddle on a field" style="left:108px;top:845px;width:241px;height:241px;border-radius:50%;background:linear-gradient(180deg,#c8c1a7,#3d5a3a 60%,#23361f)"></div>

  <h2 class="h2" style="left:647px;top:785px"><span class="blue">COFFEE WITH A</span><br>PURPOSE</h2>
  <div class="copy" style="left:647px;top:873px;width:420px">
    <p>Heart of the Andes Coffee Co. operates as a large-scale coffee growing and harvesting company located within the community of Loja, Ecuador.</p>
    <p>For over 100 years, we have been known as the most reliable distributor &amp; brewer of high quality Arabica beans throughout the South American region, according to our satisfied &amp; consistent customer base! We have the experience &amp; knowledge to support the consistent qulity of our product.</p>
    <p>We can assure you that our coffee will make the perfect fundraising product for friends, family and anyone who would like to support the organization of your choice!</p>
  </div>
  <div class="btn" style="left:645px;top:1105px;width:122px">SHOP NOW</div>
</section>

<svg class="abs" style="left:0;top:1215px" width="1200" height="780" viewBox="0 0 1200 780">
  <path d="M0 20 C200 -10 420 40 640 28 C860 16 1000 -20 1200 30 L1200 730 C1000 680 820 760 600 745 C380 730 200 700 0 760Z" fill="var(--blue-light)"/>
</svg>
<h2 class="h2" style="left:0;top:1352px;width:1200px;text-align:center"><span class="blue">DIFFRENT</span> COFFEE FLAVORS</h2>
<div class="flavors-sub">Our Coffee comes in three Different Roasts:</div>

<article class="card" style="left:128px">
  <div class="beans" role="img" aria-label="Roasted coffee beans background"></div>
  <div class="bag" role="img" aria-label="Labelled medium roast coffee bag product"></div>
  <h4>MEDIUM ROAST</h4><div class="size">(12 oz)</div><div class="price">$15</div>
  <div class="btn">SHOP NOW</div>
</article>
<article class="card" style="left:451px">
  <div class="beans" role="img" aria-label="Roasted coffee beans background"></div>
  <div class="bag" role="img" aria-label="Labelled dark roast coffee bag product"></div>
  <h4>DARK ROAST</h4><div class="size">(12 oz)</div><div class="price">$15</div>
  <div class="btn">SHOP NOW</div>
</article>
<article class="card" style="left:772px">
  <div class="beans" role="img" aria-label="Roasted coffee beans background"></div>
  <div class="bag" role="img" aria-label="Labelled French roast coffee bag product"></div>
  <h4>FRENCH ROAST</h4><div class="size">(12 oz)</div><div class="price">$15</div>
  <div class="btn">SHOP NOW</div>
</article>

<h3 class="h3" style="left:169px;top:2104px">I SELL COFFEE TO<br>SPORTS TEAMS</h3>
<div class="copy" style="left:173px;top:2188px;width:345px">Our Arabica beans are grown at an altitude of 1600–2100' with a humidity level of 10.5–11.5%. These are prime growing conditions to produce a high level of quality and flavor levels for this type of bean.</div>
<div class="btn" style="left:171px;top:2284px;width:140px">LEARN MORE</div>
<div class="photo" role="img" aria-label="Basketball game in a lit arena" style="left:659px;top:2065px;width:360px;height:285px;border-radius:20px 4px 20px 4px;background:linear-gradient(180deg,#1c2c4a,#3a4b6e 45%,#b5895a 75%,#8a6036)"></div>
<div class="ring" style="left:928px;top:2318px"></div>

<div class="photo" role="img" aria-label="Espresso grinder filling a portafilter with ground coffee" style="left:171px;top:2423px;width:362px;height:382px;border-radius:4px 60px 4px 20px;background:radial-gradient(circle at 55% 55%,#a4622c,#3a2416 45%,#141010 85%)"></div>
<div class="ring" style="left:143px;top:2475px"></div>
<h3 class="h3" style="left:659px;top:2461px">THE MOST AMAZING<br>COFFEE STATISTICS</h3>
<ul class="stats">
  <li><svg width="14" height="14" viewBox="0 0 14 14"><circle cx="7" cy="7" r="6" fill="none" stroke="var(--blue)" stroke-width="1.5"/><path d="M4 7l2 2 4-4" fill="none" stroke="var(--blue)" stroke-width="1.5"/></svg>64% of American Adults Currently Consume coffee every day !</li>
  <li><svg width="14" height="14" viewBox="0 0 14 14"><circle cx="7" cy="7" r="6" fill="none" stroke="var(--blue)" stroke-width="1.5"/><path d="M4 7l2 2 4-4" fill="none" stroke="var(--blue)" stroke-width="1.5"/></svg>Americans drink about 400 million cups of coffee every day.</li>
  <li><svg width="14" height="14" viewBox="0 0 14 14"><circle cx="7" cy="7" r="6" fill="none" stroke="var(--blue)" stroke-width="1.5"/><path d="M4 7l2 2 4-4" fill="none" stroke="var(--blue)" stroke-width="1.5"/></svg>Americans drink about 146 billion cups of coffee per year.</li>
  <li><svg width="14" height="14" viewBox="0 0 14 14"><circle cx="7" cy="7" r="6" fill="none" stroke="var(--blue)" stroke-width="1.5"/><path d="M4 7l2 2 4-4" fill="none" stroke="var(--blue)" stroke-width="1.5"/></svg>66% of women drink coffee every day, compared to 62% of men</li>
  <li><svg width="14" height="14" viewBox="0 0 14 14"><circle cx="7" cy="7" r="6" fill="none" stroke="var(--blue)" stroke-width="1.5"/><path d="M4 7l2 2 4-4" fill="none" stroke="var(--blue)" stroke-width="1.5"/></svg>66% of women drink coffee every day, compared to 62% of men</li>
  <li><svg width="14" height="14" viewBox="0 0 14 14"><circle cx="7" cy="7" r="6" fill="none" stroke="var(--blue)" stroke-width="1.5"/><path d="M4 7l2 2 4-4" fill="none" stroke="var(--blue)" stroke-width="1.5"/></svg>79% of Americans prepare coffee at home.</li>
</ul>
<div class="btn" style="left:661px;top:2735px;width:140px">LEARN MORE</div>

<h3 class="h3" style="left:169px;top:2925px">WE ARE WITH YOU EVERY<br>STEP OF THE WAY</h3>
<div class="copy" style="left:173px;top:3010px;width:355px">If you any questions or concerns, please feel free to reach out to me, Dario Velmont. My contact information is listed in the beginning of this brochure. We know the recipients of our fine coffee will enjoy it as much as we do</div>
<div class="btn" style="left:171px;top:3105px;width:140px">LEARN MORE</div>
<div class="photo" role="img" aria-label="Smiling person working at a laptop in a bright office" style="left:659px;top:2885px;width:360px;height:283px;border-radius:4px 20px 4px 20px;background:linear-gradient(180deg,#e2ddd3,#b9a58a 55%,#6d5a45)"></div>
<div class="ring" style="left:632px;top:3088px"></div>

<section class="abs reviews">
  <div class="halo"></div>
  <h2>CLIENT <span class="dark">REVIEWS</span></h2>
  <div class="sub">What Our client say about Us !</div>
  <div class="review" style="left:106px"><div class="q">“</div><p>Lorem Ipsum has been the industry's standard dummy text ever since the when an unknown printer took a galley of type and scrambled it to make a type.</p><div class="who">–&nbsp;&nbsp; Client Name</div><div class="stars">★★★★★</div></div>
  <div class="review" style="left:441px"><div class="q">“</div><p>Lorem Ipsum has been the industry's standard dummy text ever since the when an unknown printer took a galley of type and scrambled it to make a type.</p><div class="who">–&nbsp;&nbsp; Client Name</div><div class="stars">★★★★★</div></div>
  <div class="review" style="left:777px"><div class="q">“</div><p>Lorem Ipsum has been the industry's standard dummy text ever since the when an unknown printer took a galley of type and scrambled it to make a type.</p><div class="who">–&nbsp;&nbsp; Client Name</div><div class="stars">★★★★★</div></div>
</section>

<h2 class="h2" style="left:0;top:3788px;width:1200px;text-align:center;line-height:42px">FUNDRAISING FOR CLUBS, SPORTS TEAMS<br>AND/OR&nbsp; ORGANIZATIONS</h2>
<div class="btn" style="left:530px;top:3893px;width:140px">GET STARTED</div>

<div class="photo" role="img" aria-label="Coffee beans being roasted with a scoop" style="left:163px;top:4027px;width:260px;height:260px;border-radius:18px;background:radial-gradient(circle at 45% 45%,#8a5128,#3e2213 70%)"></div>
<div class="photo" role="img" aria-label="Hands holding latte cups" style="left:460px;top:4081px;width:111px;height:111px;border-radius:14px;background:linear-gradient(160deg,#8f6a4b,#d8c2a4 60%,#5c3d27)"></div>
<div class="photo" role="img" aria-label="Barista checking a tablet in a café" style="left:592px;top:3975px;width:174px;height:169px;border-radius:14px;background:linear-gradient(180deg,#c9ccd0,#7d8490 50%,#3a3f47)"></div>
<div class="photo" role="img" aria-label="Barista pouring coffee behind a counter" style="left:443px;top:4164px;width:190px;height:188px;border-radius:14px;background:linear-gradient(180deg,#d8d6cf,#9a8e7f 55%,#4a3d32)"></div>
<div class="photo" role="img" aria-label="Student smiling with a coffee cup" style="left:657px;top:4181px;width:109px;height:108px;border-radius:14px;background:linear-gradient(180deg,#d29b5c,#6a4a34)"></div>
<div class="photo" role="img" aria-label="Group of students walking on campus" style="left:792px;top:4046px;width:245px;height:245px;border-radius:18px;background:linear-gradient(180deg,#dfe6ec,#b9c3cc 40%,#c88e4d 70%,#6b7a8c)"></div>

<svg class="abs" style="left:0;top:4410px" width="1200" height="371" viewBox="0 0 1200 371">
  <path d="M0 50 C240 10 470 35 700 30 C900 25 1060 -5 1200 10 L1200 371 L0 371Z" fill="var(--blue-light)" opacity=".7"/>
  <path d="M0 60 C260 30 480 55 700 48 C900 42 1060 20 1200 38 L1200 371 L0 371Z" fill="var(--blue-mid)"/>
</svg>
<footer>
  <div class="abs" style="left:59px;top:4512px;font-size:52px;color:var(--blue-dark)">Lumvek</div>
  <div class="abs" style="left:59px;top:4583px;display:flex;align-items:center;gap:14px;font-size:11px;color:var(--white)">
    <svg width="16" height="16" viewBox="0 0 24 24"><path fill="var(--blue-dark)" d="M6.6 10.8a15 15 0 0 0 6.6 6.6l2.2-2.2c.3-.3.7-.4 1-.2 1.1.4 2.3.6 3.6.6.6 0 1 .4 1 1V20c0 .6-.4 1-1 1A17 17 0 0 1 3 4c0-.6.4-1 1-1h3.5c.6 0 1 .4 1 1 0 1.3.2 2.5.6 3.6.1.3 0 .7-.2 1z"/></svg>555-014-2398
  </div>
  <div class="abs" style="left:59px;top:4607px;display:flex;align-items:center;gap:14px;font-size:11px;color:var(--white)">
    <svg width="17" height="13" viewBox="0 0 24 18"><rect x="1" y="1" width="22" height="16" rx="2" fill="var(--blue-dark)"/><path d="M2 2l10 8 10-8" fill="none" stroke="#fff" stroke-width="2"/></svg>hello@lumvekmail.com
  </div>
  <div class="abs" style="left:59px;top:4641px;width:32px;height:32px;border-radius:50%;background:var(--blue-dark)" aria-label="Social profile"></div>
  <div class="abs" style="left:99px;top:4641px;width:32px;height:32px;border-radius:50%;background:var(--blue-dark)" aria-label="Social profile"></div>

  <div class="footer-h" style="left:336px">RESOURCES</div>
  <ul class="links" style="left:340px"><li>Help Center</li><li>Blog</li><li>Fundraise</li><li>Login</li><li>Fundraise</li><li>Customize</li></ul>

  <div class="footer-h" style="left:610px">COMPANY</div>
  <ul class="links" style="left:614px"><li>About</li><li>Careers</li><li>Reviews</li><li>Contact</li><li>Privacy</li><li>Terms</li></ul>

  <div class="footer-h" style="left:887px">NEWSLETTER SIGNUP !</div>
  <div class="abs" style="left:887px;top:4557px;width:240px;font-size:11px;line-height:19px;color:var(--white)">Would you like to receive our exclusive update for signup !</div>
  <div class="abs" style="left:887px;top:4614px;width:250px;height:40px;border-radius:20px;background:var(--white);font-size:11px;color:var(--muted);padding:12px 16px">Enter Email</div>
  <div class="abs" style="left:1100px;top:4618px;width:32px;height:32px;border-radius:50%;background:var(--blue-dark);display:flex;align-items:center;justify-content:center">
    <svg width="14" height="14" viewBox="0 0 24 24"><path d="M2 12l20-9-7 19-3-8z" fill="#fff"/></svg>
  </div>

  <div class="abs" style="left:0;top:4746px;width:1200px;text-align:center;font-size:11px;color:var(--white)">© <span style="color:var(--blue-dark)">Lumvek</span> – 2021 All rights reserved.</div>
</footer>

</body>
</html>
```